Lumora Systems New Website - IT Infrastructure | Smart Cabinet | Micro Data Center

We're an IT SI providing Server Room Design & Build | All-in-One Rack & Smart Cabinet | Structured Cabling | IT Relocation | Maintenance. Old website can be found at www.lumorasys.com.hk. We'd like a brand new wix website which is modern, minimalist, interactive with some animation. Website content will be mostly static and include our service, our project, news and events, about us, contacts, blogs, partners and brands, etc.

reference sites:
We'd like to see more designs referring to below

https://www.pixelvane.example/design/41736205
https://www.pixelvane.example/design/41892417
https://velbrinn.example/

Animation (scrolling effect) referring to
https://velbrinn.example/intelligence/smart-office-room/
Updates

we'd like below style.

Designs look the same

Target Market(s)

Commercials in HK

Industry/Entity Type

IT, Technology, Data Center

Coding

Coded - Design and coding required

Font styles to use
Sans Serif

Requirements
Must have
• CMS, Some Interactive Elements/ Graphics

```html
<!DOCTYPE html>
<html lang="en">
<head>
<meta charset="utf-8">
<title>Lumora Systems — IT Infrastructure</title>
<link href="https://fonts.googleapis.com/css2?family=Fira+Sans:wght@400;500;600;700&family=Lato:wght@400;700;900&display=swap" rel="stylesheet">
<style>
:root{
  --navy:#2b465f;
  --navy-deep:#0f1d2c;
  --ink:#1c2b3a;
  --orange:#ff7200;
  --grey-bg:#f2f2f2;
  --text:#6c737b;
  --line:#d9dde1;
  --white:#fff;
}
*{margin:0;padding:0;box-sizing:border-box}
html,body{width:1200px;height:4967px;overflow:hidden;background:var(--white)}
body{font-family:"Lato",sans-serif;color:var(--text);position:relative}
.abs{position:absolute}
h1,h2,h3,h4{font-family:"Fira Sans",sans-serif;color:var(--navy);font-weight:600}

/* top bar */
.topbar{top:0;left:0;width:1200px;height:106px;background:#f7f7f7}
.brand{font-family:"Fira Sans",sans-serif;font-weight:600;color:var(--orange);display:flex;align-items:center;gap:8px}
.brand .mark{width:22px;height:22px;border:3px solid var(--orange);border-radius:3px}
.top-brand{left:102px;top:20px;font-size:22px}
.info{display:flex;gap:12px;align-items:center;font-size:11px;color:var(--ink)}
.info b{display:block;font-weight:700;font-size:10px;letter-spacing:.3px}
.info-loc{left:428px;top:22px}
.info-hours{left:678px;top:22px}
.divider-v{left:652px;top:18px;width:1px;height:46px;background:#c7c7c7}
.btn-appoint{left:944px;top:20px;width:168px;height:46px;background:#14314f;color:#fff;font:900 11px "Lato",sans-serif;display:flex;align-items:center;justify-content:center;border-radius:3px}

.nav{left:85px;top:77px;width:1053px;height:64px;background:#fff;box-shadow:0 4px 14px rgba(0,0,0,.08);z-index:3;display:flex;align-items:center;font-size:13px;color:#3c4a57}
.nav a{position:absolute;text-decoration:none;color:inherit}
.nav .soc{position:absolute;top:14px;width:34px;height:34px;border-radius:3px}

/* hero */
.hero{top:106px;left:0;width:1200px;height:686px;background:
  radial-gradient(ellipse 320px 500px at 180px 360px,rgba(255,120,40,.45),transparent 70%),
  radial-gradient(ellipse 300px 500px at 1050px 360px,rgba(40,170,200,.4),transparent 70%),
  linear-gradient(180deg,#25303c,#1a2430 60%,#10171f)}
.hero-shade{top:106px;left:0;width:1200px;height:686px;background:rgba(10,16,24,.35)}
.badge-welcome{left:511px;top:330px;width:162px;height:35px;background:#2e4560;color:#fff;font:700 11px "Lato",sans-serif;display:flex;align-items:center;justify-content:center;border-radius:2px}
.hero-title{left:0;top:378px;width:1200px;text-align:center;color:#fff;font-size:62px;line-height:73px;font-weight:600}
.btn-ghost{left:507px;top:546px;width:168px;height:48px;border:2px solid #fff;color:#fff;font:700 11px "Lato",sans-serif;display:flex;align-items:center;justify-content:center;border-radius:3px}
.hero-arrow{top:488px;width:62px;height:62px;background:#fff;border-radius:3px;display:flex;align-items:center;justify-content:center}

/* about */
.about-photo{left:98px;top:922px;width:442px;height:434px;border-radius:50%;background:radial-gradient(circle at 55% 45%,#c9c4bd,#56687a 55%,#1f3142)}
.float-badge{left:434px;top:1250px;width:96px;height:96px;border-radius:50%;background:#fff;box-shadow:0 6px 18px rgba(0,0,0,.15);display:flex;align-items:center;justify-content:center}
.eyebrow{font:700 10px "Lato",sans-serif;color:var(--orange);letter-spacing:.3px;display:flex;align-items:center;gap:14px}
.eyebrow::after{content:"";width:46px;height:2px;background:var(--orange)}
.eyebrow.center::before{content:"";width:46px;height:2px;background:var(--orange)}
.about-eyebrow{left:611px;top:942px}
.about-title{left:609px;top:966px;font-size:46px;line-height:64px;width:560px;white-space:nowrap}
.about-text{left:611px;top:1105px;width:440px;font-size:12.5px;line-height:24.5px}
.btn-orange{background:var(--orange);color:#fff;font:700 13px "Lato",sans-serif;display:flex;align-items:center;justify-content:center;border-radius:4px}
.about-btn{left:611px;top:1294px;width:168px;height:45px}

/* services */
.services{top:1460px;left:0;width:1200px;height:820px;background:var(--grey-bg)}
.svc-eyebrow{left:89px;top:1544px}
.svc-title{left:88px;top:1575px;font-size:46px}
.svc-arrow{top:1559px;width:45px;height:63px;background:#fff;box-shadow:0 2px 8px rgba(0,0,0,.08);display:flex;align-items:center;justify-content:center}
.card{top:1682px;width:320px;height:313px;border-radius:4px;overflow:hidden}
.card .ph{position:absolute;inset:0;background:linear-gradient(160deg,#5b7287,#24374b 60%,#111c27)}
.card .ph::after{content:"";position:absolute;inset:0;background:linear-gradient(180deg,rgba(0,0,0,.1),rgba(0,0,0,.55))}
.card .ic{position:absolute;left:42px;top:46px;width:66px;height:66px;background:#fff;border-radius:6px;display:flex;align-items:center;justify-content:center}
.card h3{position:absolute;left:34px;top:146px;color:#fff;font-size:23px;font-weight:500}
.card p{position:absolute;left:34px;top:214px;color:#fff;font-size:12.5px}
.card .more{position:absolute;left:34px;top:253px;color:#fff;font:700 15px "Lato",sans-serif}
.card .bar{position:absolute;left:34px;top:279px;width:252px;height:3px;background:var(--orange)}
.svc-btn{left:511px;top:2068px;width:168px;height:48px}

.cta{left:95px;top:2178px;width:1016px;height:208px;border-radius:8px;background:linear-gradient(90deg,#1d2c40,#2b3e58 45%,#3b4b66 70%,#1c2b42)}
.cta-text{left:130px;top:2272px;color:#fff;font:600 24px "Fira Sans",sans-serif}
.cta-quote{left:683px;top:2263px;width:164px;height:52px;border:1px solid #fff;color:#fff;font:700 14px "Lato",sans-serif;display:flex;align-items:center;justify-content:center}
.cta-phone{left:855px;top:2263px;width:204px;height:52px;background:#fff;color:var(--ink);font:700 15px "Lato",sans-serif;display:flex;align-items:center;justify-content:center;gap:10px}

/* why */
.why-eyebrow{left:0;top:2444px;width:1200px;justify-content:center}
.why-title{left:0;top:2468px;width:1200px;text-align:center;font-size:46px}
.why-photo{left:434px;top:2575px;width:330px;height:367px;border-radius:50%;background:radial-gradient(circle at 50% 40%,#9aa3ab,#3d5268 60%,#223447)}
.feat{width:260px}
.feat h4{font-size:20px;font-weight:500;margin-bottom:6px}
.feat p{font-size:12.5px;line-height:17px}
.feat.l{text-align:right}
.fic{width:64px;height:64px;border-radius:50%;background:#fff;box-shadow:0 4px 14px rgba(0,0,0,.1);display:flex;align-items:center;justify-content:center}

/* reviews */
.reviews{top:3058px;left:0;width:1200px;height:532px;background:var(--grey-bg)}
.reviews-photo{left:0;top:3058px;width:338px;height:532px;background:linear-gradient(180deg,#1a3450,#0f2236 60%,#0a1726)}
.rev-eyebrow{left:338px;top:3119px;width:862px;justify-content:center}
.rev-title{left:338px;top:3143px;width:862px;text-align:center;font-size:46px}
.rev{top:3260px;width:347px;height:203px;background:#fff;border-radius:6px;box-shadow:0 4px 14px rgba(0,0,0,.08);padding:26px 24px;font-size:12.5px;line-height:23px}
.rev .who{position:absolute;left:22px;bottom:20px;display:flex;align-items:center;gap:12px;font:700 12px "Lato",sans-serif;color:var(--ink)}
.rev .av{width:48px;height:48px;border-radius:50%;background:linear-gradient(135deg,#8fa0ae,#5a6d7d)}
.rev .q{position:absolute;right:26px;bottom:44px}
.dot{top:3508px;width:9px;height:9px;border-radius:50%;background:#b9c0c6}

/* contact */
.c-eyebrow{left:0;top:3713px;width:1200px;justify-content:center}
.c-title{left:0;top:3737px;width:1200px;text-align:center;font-size:46px}
.c-box{left:91px;top:3844px;width:1018px;height:415px;background:#fff;box-shadow:0 4px 20px rgba(0,0,0,.08)}
.c-photo{left:91px;top:3844px;width:420px;height:415px;background:linear-gradient(150deg,#4d6378,#1d3044 65%,#0f1e2e)}
.c-phone{left:285px;top:4176px;width:197px;height:58px;background:#fff;color:var(--ink);font:700 16px "Lato",sans-serif;display:flex;align-items:center;justify-content:center;gap:10px;border-radius:2px}
.f-title{left:554px;top:3890px;font-size:24px;font-weight:500}
.f-sub{left:554px;top:3930px;width:500px;font-size:13px;line-height:22px}
.input{border:1px solid #cfd4d8;border-radius:3px;height:48px;font-size:12px;color:#9aa1a8;padding:0 16px;display:flex;align-items:center}
.f-btn{left:554px;top:4151px;width:501px;height:46px;font-size:11px;gap:8px}

/* footer */
.f-slant{left:115px;top:4369px;width:970px;height:40px;background:#dce5ee;clip-path:polygon(2% 0,100% 60%,100% 100%,0 100%)}
.footer{top:4408px;left:0;width:1200px;height:501px;background:var(--navy-deep)}
.f-strip{left:85px;top:4408px;width:1030px;height:148px;background:#fff}
.strip-item{top:4452px;width:300px;text-align:center;font:700 15px "Lato",sans-serif;color:var(--ink)}
.strip-item svg{display:block;margin:0 auto 12px}
.strip-sep{top:4436px;width:1px;height:92px;background:#e1e4e7}
.foot-brand{left:91px;top:4620px;font-size:36px}
.foot-brand .mark{width:40px;height:40px;border-width:4px}
.foot-p{left:85px;top:4686px;width:320px;font-size:13px;line-height:22px;color:#c5ccd3}
.foot-h{top:4620px;color:#fff;font:600 17px "Fira Sans",sans-serif}
.foot-t{font-size:13px;color:#c5ccd3}
.foot-sub{left:438px;top:4793px;width:307px;height:41px;border:1px solid #c5ccd3;display:flex;font-size:11px}
.foot-sub span{flex:1;padding:0 12px;display:flex;align-items:center;color:#c5ccd3}
.foot-sub b{width:102px;border-left:1px solid #c5ccd3;color:var(--orange);display:flex;align-items:center;justify-content:center;font-weight:900;font-size:13px}
.bottom{top:4909px;left:0;width:1200px;height:58px;background:#e7edf3}
.bottom-t{left:86px;top:4931px;font:700 11px "Lato",sans-serif;color:var(--ink)}
.b-soc{top:4929px;width:14px;height:14px;border-radius:50%;background:var(--ink)}
.totop{left:1138px;top:4900px;width:50px;height:50px;background:var(--orange);border-radius:4px;display:flex;align-items:center;justify-content:center}
</style>
</head>
<body>

<!-- Header -->
<div class="abs topbar"></div>
<div class="abs brand top-brand"><span class="mark"></span>Lumora</div>
<div class="abs info info-loc">
  <svg width="28" height="30" viewBox="0 0 24 24" fill="none" stroke="#1c2b3a" stroke-width="1.6"><path d="M12 22s7-7 7-12a7 7 0 0 0-14 0c0 5 7 12 7 12z"/><circle cx="12" cy="10" r="2.5"/></svg>
  <div><b>LOCATION</b>88 Harlow Ln, Kowloon</div>
</div>
<div class="abs divider-v"></div>
<div class="abs info info-hours">
  <svg width="32" height="32" viewBox="0 0 24 24" fill="none" stroke="#1c2b3a" stroke-width="1.6"><circle cx="12" cy="12" r="9"/><path d="M8 12h8M13 9l3 3-3 3"/></svg>
  <div><b>OFFICE HOURS</b>9.00 to 7.00 [Sun: Closed]</div>
</div>
<div class="abs btn-appoint">MAKE APPOINTMENT</div>

<nav class="abs nav">
  <a style="left:34px">Home</a>
  <a style="left:136px">About Us</a>
  <a style="left:268px">Services</a>
  <a style="left:396px">Our Team</a>
  <a style="left:510px">Blog</a>
  <a style="left:609px">Gallery</a>
  <a style="left:709px">Contact Us</a>
  <span class="soc" style="left:864px;background:#3d5a98"></span>
  <span class="soc" style="left:910px;background:#e0263b"></span>
  <span class="soc" style="left:956px;background:#3aa4e8"></span>
</nav>

<!-- Hero -->
<div class="abs hero" role="img" aria-label="Server room aisle with glowing rack lights"></div>
<div class="abs hero-shade"></div>
<div class="abs badge-welcome">WELCOME</div>
<h1 class="abs hero-title">Architects of Resilient<br>Data Foundations.</h1>
<div class="abs btn-ghost">LEARN MORE</div>
<div class="abs hero-arrow" style="left:42px"><svg width="20" height="20" viewBox="0 0 24 24" fill="none" stroke="#1c2b3a" stroke-width="2.2"><path d="M20 12H4M10 6l-6 6 6 6"/></svg></div>
<div class="abs hero-arrow" style="left:1094px"><svg width="20" height="20" viewBox="0 0 24 24" fill="none" stroke="#1c2b3a" stroke-width="2.2"><path d="M4 12h16M14 6l6 6-6 6"/></svg></div>

<!-- About -->
<div class="abs about-photo" role="img" aria-label="Engineer on a phone call in a server room"></div>
<div class="abs float-badge"><span style="width:34px;height:34px;border:4px solid var(--orange);border-radius:4px"></span></div>
<div class="abs eyebrow about-eyebrow">ABOUT US</div>
<h2 class="abs about-title">Where Reliability<br>Meets Connectivity</h2>
<p class="abs about-text">Lorem ipsum dolor sit amet, consectetur adipiscing elit, sed do eiusmod tempor incididunt ut labore et dolore magna aliqua. Ut enim ad minim veniam, quis nostrud exercitation ullamco laboris nisi ut aliquip ex ea commodo consequat. Duis aute irure dolor in reprehenderit in voluptate velit esse cillum dolore eu fugiat nulla pariatur. Excepteur sint occaecat cupidatat non proident, sunt in culpa qui officia deserunt mollit anim id est laborum.</p>
<div class="abs btn-orange about-btn">Learn More</div>

<!-- Services -->
<div class="abs services"></div>
<div class="abs eyebrow svc-eyebrow">SERVICES</div>
<h2 class="abs svc-title">Our Services</h2>
<div class="abs svc-arrow" style="left:999px"><svg width="16" height="16" viewBox="0 0 24 24" fill="none" stroke="#111" stroke-width="3"><path d="M15 5l-7 7 7 7"/></svg></div>
<div class="abs svc-arrow" style="left:1051px"><svg width="16" height="16" viewBox="0 0 24 24" fill="none" stroke="#111" stroke-width="3"><path d="M9 5l7 7-7 7"/></svg></div>

<div class="abs card" style="left:93px">
  <div class="ph" role="img" aria-label="Technician with laptop beside server racks"></div>
  <div class="ic"><svg width="34" height="34" viewBox="0 0 24 24" fill="none" stroke="#2b465f" stroke-width="2" stroke-linecap="round"><path d="M12 3v3M12 18v3M3 12h3M18 12h3M5.6 5.6l2.1 2.1M16.3 16.3l2.1 2.1M5.6 18.4l2.1-2.1M16.3 7.7l2.1-2.1"/></svg></div>
  <h3>Data Centre Building</h3>
  <p>Lorem ipsum dolor sit amet, consectetur</p>
  <span class="more">Meer Leren</span><span class="bar"></span>
</div>
<div class="abs card" style="left:440px">
  <div class="ph" role="img" aria-label="Patch panel with structured network cabling"></div>
  <div class="ic"><svg width="34" height="34" viewBox="0 0 24 24" fill="none" stroke="#2b465f" stroke-width="2"><circle cx="12" cy="12" r="9"/><path d="M9 9l-3 3 3 3M15 9l3 3-3 3"/></svg></div>
  <h3>Structured Cabling</h3>
  <p>Lorem ipsum dolor sit amet, consectetur</p>
  <span class="more">Meer Leren</span><span class="bar"></span>
</div>
<div class="abs card" style="left:787px">
  <div class="ph" role="img" aria-label="Row of blue lit server cabinets"></div>
  <div class="ic"><svg width="34" height="34" viewBox="0 0 24 24" fill="none" stroke="#2b465f" stroke-width="2"><path d="M4 6h16"/><circle cx="8" cy="14" r="3"/><circle cx="16" cy="14" r="3"/><path d="M4 10h16"/></svg></div>
  <h3>Audio-Visual</h3>
  <p>Lorem ipsum dolor sit amet, consectetur</p>
  <span class="more">Meer Leren</span><span class="bar"></span>
</div>
<div class="abs btn-orange svc-btn">Learn More</div>

<div class="abs cta" role="img" aria-label="Data centre corridor banner"></div>
<div class="abs cta-text">Architects of Seamless Connectivity</div>
<div class="abs cta-quote">Get A Quote</div>
<div class="abs cta-phone"><svg width="18" height="18" viewBox="0 0 24 24" fill="#1c2b3a"><path d="M6.6 10.8a15 15 0 0 0 6.6 6.6l2.2-2.2a1 1 0 0 1 1-.25 11.4 11.4 0 0 0 3.6.6 1 1 0 0 1 1 1V20a1 1 0 0 1-1 1A17 17 0 0 1 3 4a1 1 0 0 1 1-1h3.5a1 1 0 0 1 1 1c0 1.25.2 2.45.6 3.6a1 1 0 0 1-.25 1z"/></svg>0852 - 417 - 3390</div>

<!-- Why choose us -->
<div class="abs eyebrow center why-eyebrow">WHY CHOSE US</div>
<h2 class="abs why-title">Why Choose Us</h2>
<div class="abs why-photo" role="img" aria-label="Smiling consultant with arms crossed"></div>

<div class="abs feat l" style="left:62px;top:2617px"><h4>Quality Services</h4><p>Lorem ipsum dolor sit amet,<br>consectetur adipiscing elit</p></div>
<div class="abs fic" style="left:363px;top:2615px"><svg width="30" height="30" viewBox="0 0 24 24" fill="none" stroke="#ff7200" stroke-width="1.8"><circle cx="12" cy="4" r="2"/><path d="M5 9h14M12 9v6l-4 6M12 15l4 6"/></svg></div>

<div class="abs feat l" style="left:37px;top:2742px"><h4>Personalized Approach</h4><p>Lorem ipsum dolor sit amet,<br>consectetur adipiscing elit</p></div>
<div class="abs fic" style="left:327px;top:2745px"><svg width="30" height="30" viewBox="0 0 24 24" fill="none" stroke="#ff7200" stroke-width="2" stroke-linecap="round"><path d="M12 3v3M12 18v3M3 12h3M18 12h3M5.6 5.6l2.1 2.1M16.3 16.3l2.1 2.1M5.6 18.4l2.1-2.1M16.3 7.7l2.1-2.1"/></svg></div>

<div class="abs feat l" style="left:46px;top:2866px"><h4>Scalable Infrastructure</h4><p>Lorem ipsum dolor sit amet,<br>consectetur adipiscing elit</p></div>
<div class="abs fic" style="left:360px;top:2868px"><svg width="30" height="30" viewBox="0 0 24 24" fill="none" stroke="#ff7200" stroke-width="1.8"><path d="M5 13a7 7 0 0 1 14 0M4 13h16v3H4zM9 16v4h6v-4"/></svg></div>

<div class="abs fic" style="left:770px;top:2615px"><svg width="30" height="30" viewBox="0 0 24 24" fill="none" stroke="#ff7200" stroke-width="1.8"><circle cx="12" cy="12" r="9"/><circle cx="12" cy="12" r="5"/><circle cx="12" cy="12" r="1.5"/></svg></div>
<div class="abs feat" style="left:892px;top:2617px"><h4>Proven Track Record</h4><p>Lorem ipsum dolor sit amet,<br>consectetur adipiscing elit</p></div>

<div class="abs fic" style="left:803px;top:2745px"><svg width="30" height="30" viewBox="0 0 24 24" fill="none" stroke="#ff7200" stroke-width="1.8"><path d="M5 13a7 7 0 0 1 14 0M4 13h16v3H4zM12 6v2"/></svg></div>
<div class="abs feat" style="left:900px;top:2742px"><h4>Customization</h4><p>Lorem ipsum dolor sit amet,<br>consectetur adipiscing elit</p></div>

<div class="abs fic" style="left:770px;top:2868px"><svg width="30" height="30" viewBox="0 0 24 24" fill="none" stroke="#ff7200" stroke-width="1.8"><rect x="3" y="3" width="5" height="5"/><rect x="16" y="3" width="5" height="5"/><rect x="3" y="16" width="5" height="5"/><rect x="16" y="16" width="5" height="5"/><path d="M8 5.5h8M5.5 8v8M18.5 8v8"/></svg></div>
<div class="abs feat" style="left:877px;top:2866px"><h4>Experienced Experts</h4><p>Lorem ipsum dolor sit amet,<br>consectetur adipiscing elit</p></div>

<!-- Reviews -->
<div class="abs reviews"></div>
<div class="abs reviews-photo" role="img" aria-label="Server cabinets glowing in a dark hall"></div>
<div class="abs eyebrow center rev-eyebrow">TESTIMONIALS</div>
<h2 class="abs rev-title">Clients Reviews</h2>

<div class="abs rev" style="left:135px">Lorem ipsum dolor sit amet, consectetur adipis por incididunt ut labore et dolore magna aliqu uis nostrud exercitation ullamco laboris nisi consequat. Duis aute irure dolor in reprehend
  <div class="who"><span class="av" role="img" aria-label="Client portrait"></span>Ravi Hollen</div>
  <svg class="q" width="24" height="20" viewBox="0 0 24 20" fill="#1c2b3a"><path d="M2 0h8v9l-4 11H2l3-10H2zM14 0h8v9l-4 11h-4l3-10h-3z"/></svg>
</div>
<div class="abs rev" style="left:500px">Lorem ipsum dolor sit amet, consectetur adipis por incididunt ut labore et dolore magna aliqu uis nostrud exercitation ullamco laboris nisi consequat. Duis aute irure dolor in reprehend
  <div class="who"><span class="av" role="img" aria-label="Client portrait"></span>Ravi Hollen</div>
  <svg class="q" width="24" height="20" viewBox="0 0 24 20" fill="#1c2b3a"><path d="M2 0h8v9l-4 11H2l3-10H2zM14 0h8v9l-4 11h-4l3-10h-3z"/></svg>
</div>
<div class="abs rev" style="left:870px;width:347px">Lorem ipsum dolor sit amet, consectetur adipis por incididunt ut labore et dolore magna aliqu uis nostrud exercitation ullamco laboris nisi consequat. Duis aute irure dolor in reprehend
  <div class="who"><span class="av" role="img" aria-label="Client portrait"></span>Ravi Hollen</div>
  <svg class="q" style="right:44px" width="24" height="20" viewBox="0 0 24 20" fill="#1c2b3a"><path d="M2 0h8v9l-4 11H2l3-10H2zM14 0h8v9l-4 11h-4l3-10h-3z"/></svg>
</div>
<span class="abs dot" style="left:634px;top:3503px;width:17px;height:17px;background:none;border:2px solid #2a8fb0"></span>
<span class="abs dot" style="left:638px;top:3507px;background:#2a8fb0"></span>
<span class="abs dot" style="left:663px"></span>
<span class="abs dot" style="left:694px"></span>
<span class="abs dot" style="left:723px"></span>

<!-- Contact -->
<div class="abs eyebrow center c-eyebrow">CONTACT US</div>
<h2 class="abs c-title">Get in touch with us</h2>
<div class="abs c-box"></div>
<div class="abs c-photo" role="img" aria-label="Smiling support engineer in a server room"></div>
<div class="abs c-phone"><svg width="18" height="18" viewBox="0 0 24 24" fill="#1c2b3a"><path d="M6.6 10.8a15 15 0 0 0 6.6 6.6l2.2-2.2a1 1 0 0 1 1-.25 11.4 11.4 0 0 0 3.6.6 1 1 0 0 1 1 1V20a1 1 0 0 1-1 1A17 17 0 0 1 3 4a1 1 0 0 1 1-1h3.5a1 1 0 0 1 1 1c0 1.25.2 2.45.6 3.6a1 1 0 0 1-.25 1z"/></svg>1877-204-918</div>
<h3 class="abs f-title">Please Fill in the form</h3>
<p class="abs f-sub">Get a free consultation from our experts, Our customer support team help you 24/7. Don't hesitate.</p>
<div class="abs input" style="left:554px;top:4010px;width:501px">Your Name</div>
<div class="abs input" style="left:554px;top:4080px;width:237px">Your Email</div>
<div class="abs input" style="left:817px;top:4080px;width:238px">Message</div>
<div class="abs btn-orange f-btn">GET IN TOUCH <svg width="14" height="14" viewBox="0 0 24 24" fill="none" stroke="#fff" stroke-width="2.4"><path d="M4 12h16M14 6l6 6-6 6"/></svg></div>

<!-- Footer -->
<div class="abs f-slant"></div>
<div class="abs footer"></div>
<div class="abs f-strip"></div>
<div class="abs strip-item" style="left:105px"><svg width="44" height="40" viewBox="0 0 24 22" fill="none" stroke="#ff7200" stroke-width="1.3"><path d="M12 14s5-5 5-8.5a5 5 0 0 0-10 0C7 9 12 14 12 14z"/><circle cx="12" cy="5.5" r="1.8"/><path d="M6 12l-4 8h20l-4-8"/></svg>Come to Our Location</div>
<div class="abs strip-sep" style="left:428px"></div>
<div class="abs strip-item" style="left:448px"><svg width="44" height="40" viewBox="0 0 24 22" fill="none" stroke="#ff7200" stroke-width="1.3"><path d="M2 8l10 7 10-7v12H2zM2 8l10-6 10 6"/></svg>Send Us an Email</div>
<div class="abs strip-sep" style="left:772px"></div>
<div class="abs strip-item" style="left:789px"><svg width="44" height="40" viewBox="0 0 24 22" fill="none" stroke="#ff7200" stroke-width="1.3"><rect x="8" y="1" width="8" height="20" rx="1.5"/><path d="M11 18h2M18 7a4 4 0 0 1 0 6M20 5a7 7 0 0 1 0 10"/></svg>Give Us a Call</div>

<div class="abs brand foot-brand"><span class="mark"></span>Lumora</div>
<p class="abs foot-p">Lorem ipsum dolor sit amet, consectetur adipi por incididunt ut labore et dolore magna aliqu uis nostrud exercitation ullamco laboris nisi ut a consequat. Duis aute irure dolor in reprehend</p>

<div class="abs foot-h" style="left:438px">Visit Our Place</div>
<div class="abs foot-t" style="left:438px;top:4686px;line-height:23px">17 Tessel Street<br>Unit 6B, Kwun Tong 00852</div>
<div class="abs foot-t" style="left:438px;top:4744px;font-weight:900;color:#fff;font-size:11px">FIND US ON MAP</div>
<div class="abs foot-sub"><span>Enter Your Email...</span><b>SUBSCRIBE</b></div>

<div class="abs foot-h" style="left:791px">Useful Links</div>
<div class="abs foot-t" style="left:789px;top:4684px;line-height:34.5px">About Us<br>Practice areas<br>Why Choose Us<br>How it works<br>News &amp; Updates</div>
<div class="abs foot-t" style="left:959px;top:4684px;line-height:34.5px">Testimonials<br>FAQs<br>Cookies<br>Contact Us<br>Privacy Policy</div>

<div class="abs bottom"></div>
<div class="abs bottom-t">Lumora Systems</div>
<span class="abs b-soc" style="left:990px"></span>
<span class="abs b-soc" style="left:1028px"></span>
<span class="abs b-soc" style="left:1066px"></span>
<span class="abs b-soc" style="left:1104px;border-radius:2px"></span>
<div class="abs totop"><svg width="20" height="20" viewBox="0 0 24 24" fill="none" stroke="#fff" stroke-width="2.6"><path d="M5 15l7-7 7 7"/></svg></div>

</body>
</html>
```